Vortaleen - Lead the Way!

Vortaleen is a new Silicon Valley company, of the pimrela founders from Berlin, which provides a "Shared Hive Circle". This platform allows the crowd to support startups with money, experts and fame. Our Vision is, that everyone should become an entrepreneur.

Pls find all brief details in the attached document
Updates

Would be nice to have a list of more social services I'm available on, like a list of pictograms of all my services:

Find me on: chattro, fennwix+, qrt, mivrel, datebloom, pohk, rplex, etc...

pls make sure to use the right font:
http://www.typelarder-demo.com/fonts/Orbitron

Target Market(s)

Main target market is those already involved in the startup industry, by fundraising, investing, advising, cofounding and working. Vortaleen brings a totaly new transparency and collaborative way of starting companies to that business.

· Entrepreneurs (looking for funding, team and community)
· Investors (looking for hot investments and )
· Experts (workers looking for startups they can work for equity)
· Incubators & Business Schools (looking for tools to advise startups)

Industry/Entity Type

It Company

Requirements
Must have
• Pls find all brief details in the attached document
Nice to have

```html
<!DOCTYPE html>
<html lang="en">
<head>
<meta charset="utf-8">
<title>Vortaleen Business Card</title>
<link rel="stylesheet" href="https://fonts.googleapis.com/css2?family=Orbitron:wght@400;500;700&display=swap">
<style>
  :root {
    --page: #ffffff;
    --card: #333333;
    --orange: #f47a20;
    --white: #ffffff;
    --rule: #b86a36;
    --faint: rgba(244, 122, 32, 0.16);
  }
  * { margin: 0; padding: 0; box-sizing: border-box; }
  html, body {
    width: 1200px; height: 900px; overflow: hidden;
    background: var(--page);
    font-family: "Orbitron", sans-serif;
    color: var(--white);
  }
  .canvas { position: relative; width: 1200px; height: 900px; }
  .card {
    position: absolute; left: 344px; width: 512px; height: 300px;
    background: var(--card);
    box-shadow: 0 4px 14px rgba(0,0,0,0.35);
    overflow: hidden;
  }
  .card--front { top: 114px; }
  .card--back { top: 484px; }

  .name-band {
    position: absolute; left: 0; top: 0; width: 100px; height: 300px;
    background: var(--orange);
  }
  .name-band__text {
    position: absolute; left: 50px; top: 166px;
    transform: translate(-50%, -50%) rotate(-90deg);
    white-space: nowrap; text-align: center; line-height: 1.15;
  }
  .person-name { display: block; font-weight: 700; font-size: 23px; }
  .person-role { display: block; font-style: italic; font-size: 19px; font-weight: 400; }

  .brand { position: absolute; left: 108px; top: 30px; }
  .brand__mark {
    width: 40px; height: 40px; border-radius: 50%;
    background: var(--orange); margin: 10px 0 10px 30px;
  }
  .brand__name { font-weight: 700; font-size: 18px; color: var(--white); padding-left: 10px; }
  .brand__tagline { font-style: italic; font-size: 13px; padding-left: 2px; }

  .front-rule {
    position: absolute; left: 100px; top: 138px; width: 392px; height: 2px;
    background: var(--rule);
  }
  .contact {
    position: absolute; right: 22px; top: 140px; text-align: right;
    font-size: 20px; line-height: 23px; list-style: none;
  }
  .social {
    position: absolute; right: 22px; top: 220px; text-align: right;
    font-size: 16px; line-height: 22px; list-style: none;
  }

  .back-glow {
    position: absolute; left: 150px; top: 150px; width: 200px; height: 200px;
    border-radius: 50%; background: var(--faint);
  }
  .pitch__title { position: absolute; left: 40px; top: 46px; font-size: 23px; font-weight: 500; }
  .back-rule {
    position: absolute; left: 36px; top: 80px; width: 436px; height: 2px;
    background: var(--rule);
  }
  .pitch__list {
    position: absolute; left: 52px; top: 96px; list-style: none;
    font-size: 21px; line-height: 29px;
  }
  .pitch__cta {
    position: absolute; left: 0; right: 0; top: 236px; text-align: center;
    color: var(--orange); font-size: 22px; font-weight: 500;
  }
</style>
</head>
<body>
<main class="canvas">
  <section class="card card--front" aria-label="Card front">
    <div class="name-band">
      <p class="name-band__text">
        <span class="person-name">Marten Olsby</span>
        <span class="person-role">Founder and CEO</span>
      </p>
    </div>
    <div class="brand">
      <div class="brand__mark"></div>
      <p class="brand__name">Vortaleen</p>
      <p class="brand__tagline">Lead the Way!</p>
    </div>
    <div class="front-rule"></div>
    <ul class="contact">
      <li>555-010-2468</li>
      <li>mo@vortaleen.com</li>
      <li>www.vortaleen.com</li>
    </ul>
    <ul class="social">
      <li>chirpa.com/martenolsby</li>
      <li>facelink.com/martenolsby</li>
      <li>linkfold.com/in/martenolsby</li>
    </ul>
  </section>

  <section class="card card--back" aria-label="Card back">
    <div class="back-glow"></div>
    <h2 class="pitch__title">Are you interested in:</h2>
    <div class="back-rule"></div>
    <ul class="pitch__list">
      <li>- Starting your own business?</li>
      <li>- Investing in hot startups?</li>
      <li>- Working for the next "Facelink"?</li>
    </ul>
    <p class="pitch__cta">Join us on facelink.com/Vortaleen</p>
  </section>
</main>
</body>
</html>
```